Heritage Hollow Business Cards

Require a business card design. <br/><br/>Needs to include logo (either round or long version) plus these details:<br/>Maya Torvell<br/>Heritage Hollow<br/>maya@kelvadtrading.com.au<br/>02 6481 7395<br/>PO Box Glenwarra NSW 2791<br/>www.heritagehollow.com.au<br/><br/>I need in an editable format so that I can create for multiple staff members. <br/><br/>

Target Market(s)

We are an online store selling renovation products to home owners are builders. Looking for a classic classy design.

Industry/Entity Type

Home And Garden

Contact Information for Business Card

Maya Torvell
Heritage Hollow
maya@kelvadtrading.com.au
02 6481 7395
PO Box Glenwarra NSW 2791
www.heritagehollow.com.au

Colors

Designer to choose colors to be used in the design.

Requirements
Must have
• Must include Logo.

```html
<!DOCTYPE html>
<html lang="en">
<head>
<meta charset="utf-8">
<title>Heritage Hollow Business Cards</title>
<link rel="stylesheet" href="https://fonts.googleapis.com/css2?family=Raleway:wght@400;500;600&display=swap">
<style>
  :root {
    --green: #00c383;
    --green-deep: #00a56f;
    --green-shade: #008f60;
    --charcoal: #2a2d35;
    --ink: #1f1f1f;
    --paper: #ffffff;
    --backdrop: #ebe6dc;
  }
  html, body {
    margin: 0;
    width: 1200px;
    height: 1200px;
    overflow: hidden;
    background: var(--backdrop);
    font-family: "Raleway", sans-serif;
  }
  .sheet {
    position: relative;
    width: 1200px;
    height: 1200px;
  }
  .card {
    position: absolute;
    left: 224px;
    width: 752px;
    height: 425px;
    background: var(--paper);
    box-shadow: 0 10px 22px rgba(0,0,0,0.25);
  }
  .card--front { top: 138px; }
  .card--back { top: 612px; }
  .card svg { display: block; width: 100%; height: 100%; }
  .name-first { fill: var(--green); font-weight: 400; }
  .name-last { fill: var(--paper); font-weight: 400; }
  .role { fill: var(--paper); font-size: 36px; font-weight: 400; }
  .contact { fill: var(--paper); font-size: 29px; font-weight: 500; }
  .icon { fill: none; stroke: var(--green); stroke-width: 5; stroke-linecap: round; stroke-linejoin: round; }
  .icon-solid { fill: var(--green); }
  .brand { fill: var(--ink); font-weight: 600; }
  .brand-ring { fill: none; stroke: var(--ink); stroke-width: 2; }
</style>
</head>
<body>
<main class="sheet">

  <section class="card card--front" aria-label="Business card front">
    <svg viewBox="0 0 1212 685" preserveAspectRatio="none" xmlns="http://www.w3.org/2000/svg">
      <polygon points="313,0 502,0 595,350 468,685 366,685 548,295" fill="var(--green)"/>
      <polygon points="430,0 502,0 595,350 548,295" fill="var(--green-deep)"/>
      <polygon points="548,295 595,350 420,685 366,685" fill="var(--green-deep)"/>
      <polygon points="595,350 468,685 420,685" fill="var(--green)"/>
      <polygon points="502,0 1212,0 1212,685 468,685 595,350" fill="var(--charcoal)"/>

      <circle class="brand-ring" cx="252" cy="331" r="180"/>
      <text class="brand" x="252" y="318" font-size="50" text-anchor="middle">Heritage</text>
      <text class="brand" x="252" y="378" font-size="50" text-anchor="middle">Hollow</text>

      <text x="696" y="150" font-size="78"><tspan class="name-first">Maya</tspan> <tspan class="name-last">Torvell</tspan></text>
      <text class="role" x="702" y="193">Director</text>

      <path class="icon" d="M648,322 c-10,6 -12,22 -2,36 c10,14 24,22 36,20 c6,-1 10,-6 8,-10 l-10,-8 c-4,-3 -8,-1 -10,2 c-8,-2 -16,-12 -16,-20 c4,-2 6,-6 4,-10 l-6,-10 c-2,-2 -3,-2 -4,0z"/>
      <text class="contact" x="718" y="353">02 6481 7395</text>

      <rect class="icon" x="636" y="402" width="54" height="36"/>
      <polyline class="icon" points="636,402 663,424 690,402"/>
      <text class="contact" x="718" y="428">maya@kelvadtrading.com.au</text>

      <circle class="icon" cx="663" cy="500" r="27"/>
      <ellipse class="icon" cx="663" cy="500" rx="11" ry="27"/>
      <line class="icon" x1="636" y1="500" x2="690" y2="500"/>
      <line class="icon" x1="663" y1="473" x2="663" y2="527"/>
      <line class="icon" x1="641" y1="486" x2="685" y2="486"/>
      <line class="icon" x1="641" y1="514" x2="685" y2="514"/>
      <text class="contact" x="716" y="510">www.heritagehollow.com.au</text>

      <path class="icon-solid" d="M664,558 a24,24 0 0 1 24,24 c0,16 -24,36 -24,36 c0,0 -24,-20 -24,-36 a24,24 0 0 1 24,-24z M664,572 a10,10 0 1 0 0.01,0z" fill-rule="evenodd"/>
      <text class="contact" x="716" y="598">PO Box Glenwarra NSW 2791</text>
    </svg>
  </section>

  <section class="card card--back" aria-label="Business card back">
    <svg viewBox="0 0 1212 685" preserveAspectRatio="none" xmlns="http://www.w3.org/2000/svg">
      <polygon points="0,0 920,0 0,280" fill="var(--green)"/>
      <polygon points="0,150 920,0 470,80 0,280" fill="var(--green-deep)" opacity="0.35"/>
      <polygon points="1212,405 1212,685 290,685 760,565" fill="var(--green)"/>
      <polygon points="1212,535 1212,685 290,685" fill="var(--green-shade)" opacity="0.3"/>

      <circle class="brand-ring" cx="160" cy="398" r="24"/>
      <text class="brand" x="210" y="430" font-size="96">Heritage Hollow</text>
    </svg>
  </section>

</main>
</body>
</html>
```